I have a logo and need to design the business card and stationery.
Updates

The uploaded logo image named as GREYMARSH CONSTRUCTION which is to be replaced to GREYMARSH CONTRACTS. Kindly add below details and submit the designs- Company name- Greymarsh Engineering Contracts LLP Name & Post- Kelvan Joshi (Designated Partner) Address- Block No.317, Wing C, Tulvo Trade Court, Manek Pural Road, Ruparel Industrial Estate, Goregaon(E), Mumbai - 400 063 Contact- +91 97415 60382 Email- kelvanjoshi@mailbrook.example Website- www.greymarshcontracts.example Contact for Letterhead- +91-22-28754193

Hi Tovin Rahul, We are liking your Design #28860835. We have suggested some changes which are mentioned in feedback. Kindly revert with it asap to finalize this design.

Colors

Designer to choose colors to be used in the design.

```html
<!DOCTYPE html>
<html lang="en">
<head>
<meta charset="utf-8">
<title>Greymarsh Contracts – Business Card</title>
<link href="https://fonts.googleapis.com/css2?family=Poppins:wght@400;500;600&display=swap" rel="stylesheet">
<style>
  :root {
    --backdrop: #2a2a2a;
    --card: #050505;
    --ink: #ffffff;
    --silver: #c9c9c9;
    --rule: #5a5a5a;
  }
  * { margin: 0; padding: 0; box-sizing: border-box; }
  html, body {
    width: 1200px; height: 866px; overflow: hidden;
    background: var(--backdrop);
    font-family: "Poppins", sans-serif;
    color: var(--ink);
  }
  .stage {
    width: 1200px; height: 866px;
    display: flex; flex-direction: column;
    align-items: center; justify-content: center; gap: 40px;
  }
  .card {
    width: 600px; height: 343px;
    background: var(--card);
    position: relative;
    box-shadow: 0 10px 28px rgba(0,0,0,.55);
  }
  /* back side */
  .card--back { display: flex; align-items: center; justify-content: center; }
  .brand { display: flex; align-items: center; gap: 14px; }
  .brand__mark { background: var(--silver); }
  .brand__name {
    font-weight: 600; color: var(--silver);
    letter-spacing: .08em; line-height: 1.1;
  }
  .card--back .brand__mark { width: 22px; height: 22px; }
  .card--back .brand__name { font-size: 30px; }

  /* front side */
  .card--front .brand { position: absolute; left: 40px; top: 38px; }
  .card--front .brand__mark { width: 14px; height: 14px; }
  .card--front .brand__name { font-size: 17px; }

  .details {
    position: absolute; right: 40px; top: 108px;
    text-align: right; width: 520px;
  }
  .person__name { font-size: 20px; font-weight: 600; letter-spacing: .03em; line-height: 1.2; }
  .person__role { font-size: 13px; font-weight: 400; margin-bottom: 14px; }
  .contact { list-style: none; }
  .contact li {
    font-size: 13px; line-height: 21px;
    display: flex; justify-content: flex-end; align-items: center; gap: 9px;
  }
  .contact svg { width: 13px; height: 13px; flex: none; }
  .divider { height: 1px; background: var(--rule); margin: 10px 0 10px 140px; }
  .company { font-size: 13px; font-weight: 600; letter-spacing: .02em; }
  .address { font-size: 12px; line-height: 18px; }
</style>
</head>
<body>
<main class="stage">
  <section class="card card--back">
    <div class="brand">
      <span class="brand__mark"></span>
      <span class="brand__name">GREYMARSH CONTRACTS</span>
    </div>
  </section>

  <section class="card card--front">
    <div class="brand">
      <span class="brand__mark"></span>
      <span class="brand__name">GREYMARSH CONTRACTS</span>
    </div>
    <div class="details">
      <p class="person__name">KELVAN JOSHI</p>
      <p class="person__role">Designated Partner</p>
      <ul class="contact">
        <li>+91 97415 60382
          <svg viewBox="0 0 16 16" fill="none" stroke="#fff" stroke-width="1.3"><rect x="1" y="1" width="14" height="14" rx="2"/><path d="M5 4l2 2-1 1.2c.6 1.3 1.5 2.2 2.8 2.8L10 9l2 2-1.2 1.3C7.5 12 4 8.5 3.7 5.2z" fill="#fff" stroke="none"/></svg>
        </li>
        <li>kelvanjoshi@mailbrook.example
          <svg viewBox="0 0 16 16" fill="none" stroke="#fff" stroke-width="1.3"><rect x="1" y="3" width="14" height="10"/><path d="M1 3l7 6 7-6"/></svg>
        </li>
        <li>www.greymarshcontracts.example
          <svg viewBox="0 0 16 16" fill="none" stroke="#fff" stroke-width="1.2"><circle cx="8" cy="8" r="6.5"/><ellipse cx="8" cy="8" rx="3" ry="6.5"/><path d="M1.5 8h13M2.5 4.8h11M2.5 11.2h11"/></svg>
        </li>
      </ul>
      <div class="divider"></div>
      <p class="company">GREYMARSH ENGINEERING CONTRACTS LLP</p>
      <p class="address">Block No.317, Wing C, Tulvo Trade Court, Manek Pural Road,<br>Ruparel Industrial Estate, Goregaon(E), Mumbai - 400 063</p>
    </div>
  </section>
</main>
</body>
</html>
```